Brand new letterhead, business card, email signature etc.

We are a financial company in London, UK. Our website is www.marlowvane.com. We're wanting a complete remodel of the company colours, letter head, business cards, email signatures, etc. Looking to keep the same font for the company name. I have upload a colour palette that we want to work with. We're looking for company letterhead for outgoing letters/ correspondence, letterhead for internal documentation, email signatures, e-letters. etc. Ultimately we will redesign the entire website also. It is important that our clients get a strong, secure, warm, trustworthy, solid feeling and first impression.
Updates

Designs look the same

Target Market(s)

Institutional investors, (ultra) high net worth individuals

Industry/Entity Type

Finance, Invesments banking.

Font styles to use
Other font styles liked:
• Current font is "Champagne & Limousines"

Requirements
Must have
• Must use the colours provided on the PDF uploaded to the portal. The purple = main colour. The red = accent colour.
Nice to have
• Nice to use same font as now for the company name "Corvane". Font is "Champagne & Limousines". Nice to have some reference to the old logo flower, but only subtle.
Should not have
• Do not use the colour red from our website. Use the colours provided on the colour palette PDF that I uploaded in the portal.

```html
<!DOCTYPE html>
<html lang="en">
<head>
<meta charset="utf-8">
<title>Corvane Letterhead</title>
<link href="https://fonts.googleapis.com/css2?family=Josefin+Sans:wght@300&family=Questrial&display=swap" rel="stylesheet">
<style>
  :root {
    --backdrop: #e9e8e6;
    --paper: #ffffff;
    --plum: #4a1f2f;
    --accent: #e0583a;
    --ink: #4a4a4a;
    --ink-soft: #5a5a5a;
    --bloom-a: #f1eded;
    --bloom-b: #f7f4f4;
  }
  * { margin: 0; padding: 0; box-sizing: border-box; }
  html, body { width: 1200px; height: 900px; overflow: hidden; background: var(--backdrop); }
  .canvas { position: relative; width: 1200px; height: 900px; }
  .letterhead {
    position: absolute; left: 295px; top: 20px;
    width: 609px; height: 860px;
    background: var(--paper);
    box-shadow: 0 4px 18px rgba(0,0,0,0.12);
    overflow: hidden;
  }
  .brand-mark {
    position: absolute; left: 61px; top: 68px;
    width: 48px; height: 48px;
    border: 1px solid var(--ink);
  }
  .brand-name {
    position: absolute; left: 121px; top: 72px;
    font-family: "Josefin Sans", sans-serif; font-weight: 300;
    font-size: 29px; letter-spacing: 5px; line-height: 40px;
    color: var(--ink); text-transform: uppercase;
  }
  .header-rule {
    position: absolute; left: 340px; right: 0; top: 93px;
    height: 2px; background: var(--accent);
  }
  .bloom {
    position: absolute; left: 136px; top: 251px;
    width: 337px; height: 357px;
    border-radius: 45% 55% 50% 50%;
    background: radial-gradient(circle at 50% 50%, var(--bloom-a), var(--bloom-b) 70%, transparent 72%);
  }
  .contact {
    position: absolute;
    font-family: "Questrial", sans-serif; font-size: 10.5px;
    color: var(--ink-soft);
    display: flex; align-items: center; gap: 10px;
  }
  .contact svg { width: 19px; height: 19px; flex: none; }
  .contact-social { left: 59px; top: 753px; }
  .contact-web { left: 59px; top: 780px; }
  .contact-mail { left: 215px; top: 751px; }
  .contact-phone { left: 215px; top: 780px; }
  .footer-band { position: absolute; left: 0; bottom: 0; width: 609px; height: 70px; }
</style>
</head>
<body>
<div class="canvas">
  <div class="letterhead">
    <div class="brand-mark"></div>
    <div class="brand-name">Corvane</div>
    <div class="header-rule"></div>

    <div class="bloom" role="img" aria-label="Faint line drawing of a large flower as a background watermark"></div>

    <div class="contact contact-social">
      <svg viewBox="0 0 20 20"><circle cx="10" cy="10" r="6" fill="var(--accent)"/></svg>
      <span>@marlowvane</span>
    </div>
    <div class="contact contact-web">
      <svg viewBox="0 0 20 20" fill="none" stroke="var(--accent)" stroke-width="1">
        <circle cx="10" cy="10" r="8"/>
        <ellipse cx="10" cy="10" rx="3.5" ry="8"/>
        <line x1="2" y1="10" x2="18" y2="10"/>
        <line x1="3.5" y1="6" x2="16.5" y2="6"/>
        <line x1="3.5" y1="14" x2="16.5" y2="14"/>
      </svg>
      <span>www.marlowvane.com</span>
    </div>
    <div class="contact contact-mail">
      <svg viewBox="0 0 20 20">
        <rect x="1" y="4" width="18" height="12" fill="var(--accent)"/>
        <path d="M1 4 L10 11 L19 4" fill="none" stroke="var(--paper)" stroke-width="1.4"/>
      </svg>
      <span>hello@marlowvane.com</span>
    </div>
    <div class="contact contact-phone">
      <svg viewBox="0 0 20 20">
        <circle cx="10" cy="10" r="9" fill="var(--accent)"/>
        <path d="M7 5.5 l1.6 2.4 -1 1.2 c0.7 1.5 1.8 2.6 3.3 3.3 l1.2 -1 2.4 1.6 -0.8 1.8 c-4 0.3 -7.8 -3.5 -7.5 -7.5z" fill="var(--paper)"/>
      </svg>
      <span>020-7946-0182</span>
    </div>

    <svg class="footer-band" viewBox="0 0 609 70" preserveAspectRatio="none">
      <path d="M0 35 H376 A34 34 0 0 0 410 1 V0 H609 V70 H0 Z" fill="var(--plum)"/>
    </svg>
  </div>
</div>
</body>
</html>
```